Cover für ein Taschenbuch zum Thema Ruhestand gesucht!
Zielgruppe
Unsere Zielgruppe sind Senioren, bzw. Menschen im Alter 50+. Es handelt sich bei dem Buch um einen Ratgeber zum Thema 'Ruhestand'. Allerdings wird das Buch ebenso von einer jüngeren Zielgruppe gekauft, da der Ratgeber auch gerne an Eltern oder Großeltern verschenkt wird.
Aufgabenstellung
siehe Dateiupload
Format: 5,25' x 8'

```html
<!DOCTYPE html>
<html lang="de">
<head>
<meta charset="utf-8">
<title>NEUE Freiheit – Buchcover</title>
<link rel="stylesheet" href="https://fonts.googleapis.com/css2?family=Noto+Serif:wght@400&family=Open+Sans:wght@400&display=swap">
<style>
  :root {
    --page-bg: #eeeeec;
    --sky-deep: #1a88c4;
    --sky-mid: #3aa2d6;
    --sky-pale: #cfe6f0;
    --haze: #f6eedd;
    --sun: #ffd76a;
    --sand-orange: #ee8a2a;
    --sand-deep: #c9561c;
    --label-blue: #2585bf;
    --ink-dark: #1b1b1b;
    --ink-light: #ffffff;
    --spine-shade: rgba(0, 0, 0, 0.18);
  }
  * { box-sizing: border-box; margin: 0; padding: 0; }
  html, body {
    width: 1200px;
    height: 2296px;
    overflow: hidden;
    background: var(--page-bg);
  }
  .canvas {
    position: relative;
    width: 1200px;
    height: 2296px;
  }
  .cover {
    position: absolute;
    left: 220px;
    top: 569px;
    width: 760px;
    height: 1158px;
    overflow: hidden;
    background: linear-gradient(180deg, var(--sky-deep) 0%, var(--sky-mid) 22%, #8cc6e2 38%, var(--sky-pale) 48%);
    box-shadow: 0 24px 50px rgba(0, 0, 0, 0.22);
  }
  .cover::before {
    content: "";
    position: absolute;
    left: 0; top: 0; bottom: 0;
    width: 14px;
    background: linear-gradient(90deg, var(--spine-shade), rgba(255,255,255,0.12) 60%, transparent);
    z-index: 3;
  }
  .cover-photo {
    position: absolute;
    left: 0; right: 0; bottom: 0;
    height: 640px;
    background:
      radial-gradient(ellipse 260px 200px at 46% 62%, #fff6d8 0%, var(--sun) 35%, rgba(255, 200, 90, 0) 75%),
      linear-gradient(180deg, rgba(207, 230, 240, 0) 0%, var(--haze) 30%, #f7c98a 55%, var(--sand-orange) 78%, var(--sand-deep) 100%);
  }
  .cover-text {
    position: relative;
    z-index: 2;
    text-align: center;
    padding: 0 40px;
  }
  .title {
    margin-top: 72px;
    font-family: "Noto Serif", Georgia, serif;
    font-weight: 400;
    font-size: 86px;
    line-height: 1;
    color: var(--ink-light);
    letter-spacing: 0.5px;
    white-space: nowrap;
  }
  .subtitle {
    margin-top: 14px;
    font-family: "Open Sans", Arial, sans-serif;
    font-size: 30px;
    color: var(--ink-light);
    white-space: nowrap;
  }
  .author {
    display: inline-block;
    margin-top: 48px;
    padding: 12px 40px;
    background: var(--label-blue);
    font-family: "Noto Serif", Georgia, serif;
    font-size: 25px;
    color: var(--ink-light);
  }
  .tagline {
    margin-top: 128px;
    font-family: "Noto Serif", Georgia, serif;
    font-size: 24px;
    line-height: 1.3;
    color: var(--ink-dark);
    white-space: nowrap;
  }
</style>
</head>
<body>
<main class="canvas">
  <section class="cover">
    <div class="cover-photo" role="img" aria-label="Foto: ein älteres Paar sitzt Hand in Hand in zwei Liegestühlen am Strand vor dem Sonnenuntergang"></div>
    <div class="cover-text">
      <h1 class="title">NEUE Freiheit</h1>
      <p class="subtitle">Die schönste Zeit liegt noch vor Ihnen!</p>
      <p class="author">Bernhard Velsing</p>
      <p class="tagline">Die wichtigsten Ideen und Ratschläge, mit denen Sie<br>Ihre Jahre nach dem Beruf voll auskosten</p>
    </div>
  </section>
</main>
</body>
</html>
```